Stationery Design Project - Hendry-Calloway

Letterhead
Size: A4 - 210mm x 297mm

With Compliments Slip
Size: DL - 210mm x 99mm

Notepad
Size: 250mm x 140mm

Presentation Folder
Size: A4

-
Hendry-Calloway Executive Search & Consulting
*Perth *Brisbane *Seoul *Hongkong

Website to be: www.hendrycalloway.com.au

Head Hunting & Recruitment Agency

Area we recruit in:
Executive & General Management
Government & Public Sector
Executive Contracting
Accounting
Banking & Financial Services
Information Technology & Telecommunications
Legal
Operations, Engineering & Construction
Human Resources
Board Appointments

Please note we love the business card design so if we can keep that design inline that would be great.

Best of luck

Neil

```html
<!DOCTYPE html>
<html lang="en">
<head>
<meta charset="utf-8">
<title>Hendry-Calloway Presentation Folder</title>
<link rel="stylesheet" href="https://fonts.googleapis.com/css2?family=Cinzel:wght@400;500&family=Open+Sans:wght@400;600&display=swap">
<style>
  :root {
    --backdrop: #e8e9ea;
    --paper: #f3f3f2;
    --ink: #3a3c40;
    --ink-soft: #6c6f74;
    --band: #111112;
    --band-text: #f2f2f2;
    --field-dark: #4a4d53;
    --field-mid: #6d7077;
    --field-light: #a9abb0;
    --mark: #55585e;
  }
  * { box-sizing: border-box; margin: 0; padding: 0; }
  html, body {
    width: 1200px; height: 960px; overflow: hidden;
    background: var(--backdrop);
  }
  .canvas {
    width: 1200px; height: 960px;
    display: flex; align-items: center; justify-content: center;
  }
  .folder {
    position: relative;
    width: 608px; height: 860px;
    background: var(--paper);
    box-shadow: 0 2px 6px rgba(0,0,0,0.12);
    overflow: hidden;
  }
  .folder__identity {
    position: absolute; top: 0; left: 0; right: 0; height: 448px;
    display: flex; flex-direction: column; align-items: center;
    padding-top: 150px;
  }
  .brand {
    display: flex; align-items: center; gap: 14px;
  }
  .brand__square {
    width: 26px; height: 26px; background: var(--mark);
  }
  .brand__name {
    font-family: "Cinzel", "Times New Roman", serif;
    font-weight: 500;
    font-size: 31px;
    letter-spacing: 1.5px;
    color: var(--ink);
  }
  .tagline {
    margin-top: 8px;
    font-family: "Cinzel", "Times New Roman", serif;
    font-weight: 400;
    font-size: 15px;
    letter-spacing: 3.2px;
    color: var(--ink-soft);
  }
  .folder__band {
    position: absolute; left: 0; right: 0; top: 448px; height: 28px;
    background: var(--band);
    display: flex; align-items: center; justify-content: flex-end;
    padding-right: 150px;
  }
  .folder__url {
    font-family: "Open Sans", Arial, sans-serif;
    font-size: 12px; font-weight: 600;
    letter-spacing: 0.6px;
    color: var(--band-text);
  }
  .folder__rule {
    position: absolute; left: 0; right: 0; top: 476px; height: 5px;
    background: var(--paper);
  }
  .folder__field {
    position: absolute; left: 0; right: 0; top: 481px; bottom: 0;
    background:
      radial-gradient(ellipse 55% 45% at 62% 28%, var(--field-light) 0%, var(--field-mid) 45%, transparent 80%),
      linear-gradient(180deg, var(--field-mid) 0%, var(--field-dark) 100%);
  }
</style>
</head>
<body>
<main class="canvas">
  <section class="folder" aria-label="Presentation folder front cover">
    <header class="folder__identity">
      <div class="brand">
        <span class="brand__square" aria-hidden="true"></span>
        <span class="brand__name">Hendry-Calloway</span>
      </div>
      <p class="tagline">Executive Search &amp; Consulting</p>
    </header>
    <div class="folder__band">
      <span class="folder__url">www.hendrycalloway.com.au</span>
    </div>
    <div class="folder__rule"></div>
    <div class="folder__field" role="img" aria-label="Large faint brand motif on a soft grey gradient"></div>
  </section>
</main>
</body>
</html>
```